Business card design for new eCommerce site focusing on integrity and strong businsess tactics

We need a business card that will stand out and be memorable. Something with color that matches our company logo colors. Think high end version of Pactivo. There are 2 logos provided. The parent company is called Amber Ledge Partners and we are presenting a new and very exciting eCommerce site called BrightHarborTrade.example.

Target Market(s)

Our target markets are in the Activities, Food and Beverage, Health and Beauty

Industry/Entity Type

Marketing

Contact Information for Business Card

We have 4 members that need cards...I will provide all info to the winner of the design contest
Business Address is
4870 West 63rd Avenue, Suite C207
Phoenix AZ 85731

Font styles to use
Serif
Sans Serif

Colors

Designer to choose colors to be used in the design.

Requirements
Must have
• The card must be memorable...should be unique in design but must exude integrity and be playful .
• I have provided several colors or our parent company...please feel free to use which ever
Nice to have
• I will leave this up to you. Feel free to use other images of your choosing that wraps around our client.....Activities, Dining, Health, Beauty
Should not have
• just dont be boring

```html
<!DOCTYPE html>
<html lang="en">
<head>
<meta charset="utf-8">
<title>Amber Ledge Partners – Business Card</title>
<link href="https://fonts.googleapis.com/css2?family=Open+Sans:wght@400;600;700&display=swap" rel="stylesheet">
<style>
  :root {
    --backdrop: #2e2e2e;
    --card: #f7f7f7;
    --card-edge: #e6e6e6;
    --lime: #8cbf3f;
    --ocean: #2f7fbf;
    --ink: #222222;
  }
  * { margin: 0; padding: 0; box-sizing: border-box; }
  html, body { width: 1200px; height: 904px; overflow: hidden; }
  body {
    background: var(--backdrop);
    font-family: "Open Sans", Arial, sans-serif;
    color: var(--ink);
  }
  .stage { position: relative; width: 1200px; height: 904px; }
  .card {
    position: absolute;
    left: 290px;
    width: 620px;
    height: 354px;
    background: linear-gradient(160deg, #ffffff 0%, var(--card) 60%, var(--card-edge) 100%);
    box-shadow: 0 10px 28px rgba(0,0,0,.45);
    overflow: hidden;
  }
  .card--front { top: 62px; }
  .card--back { top: 480px; }

  /* front */
  .brand-lockup {
    position: absolute; left: 70px; top: 160px;
    display: flex; align-items: center; gap: 14px;
  }
  .brand-dot { width: 30px; height: 30px; border-radius: 50%; background: var(--ocean); flex: none; }
  .brand-name { font-size: 26px; font-weight: 700; color: var(--lime); line-height: 1; white-space: nowrap; }

  /* back */
  .partner-lockup { position: absolute; left: 48px; top: 52px; }
  .partner-mark { width: 120px; height: 120px; border-radius: 50%; background: var(--lime); margin-left: 8px; }
  .partner-name { font-size: 26px; font-weight: 700; color: var(--lime); margin-top: 12px; line-height: 1; white-space: nowrap; }
  .person { position: absolute; right: 40px; top: 56px; text-align: right; }
  .person-name { font-size: 22px; font-weight: 700; color: var(--lime); line-height: 1.1; }
  .person-role { font-size: 14px; color: var(--ink); }
  .person-rule { position: absolute; right: 40px; top: 112px; width: 160px; height: 1.5px; background: var(--ink); }
  .base-rule { position: absolute; left: 40px; right: 40px; top: 232px; height: 1.5px; background: var(--ink); }
  .address { position: absolute; left: 50px; top: 248px; font-size: 15px; line-height: 1.45; font-style: normal; }
  .divider { position: absolute; left: 318px; top: 244px; width: 1.5px; height: 70px; background: var(--ink); }
  .contact { position: absolute; left: 338px; top: 248px; list-style: none; font-size: 15px; line-height: 1.45; }
  .contact li { display: flex; align-items: center; gap: 10px; white-space: nowrap; }
  .contact svg { width: 13px; height: 13px; fill: var(--lime); flex: none; }
</style>
</head>
<body>
<main class="stage">
  <section class="card card--front" aria-label="Card front">
    <div class="brand-lockup">
      <div class="brand-dot" aria-hidden="true"></div>
      <div class="brand-name">BrightHarborTrade.example</div>
    </div>
  </section>

  <section class="card card--back" aria-label="Card back">
    <div class="partner-lockup">
      <div class="partner-mark" aria-hidden="true"></div>
      <div class="partner-name">Amber Ledge Partners</div>
    </div>

    <div class="person">
      <div class="person-name">Dana Reyes</div>
      <div class="person-role">Manager</div>
    </div>
    <div class="person-rule"></div>

    <div class="base-rule"></div>
    <address class="address">
      4870 West 63rd Avenue<br>
      Suite C207<br>
      Phoenix AZ 85731
    </address>
    <div class="divider"></div>
    <ul class="contact">
      <li><svg viewBox="0 0 16 16" aria-hidden="true"><path d="M3 1l3 3-1.5 2a9 9 0 0 0 5.5 5.5L12 10l3 3-2 2C7 15 1 9 1 3z"/></svg>+999 9999 9999</li>
      <li><svg viewBox="0 0 16 16" aria-hidden="true"><path d="M1 3h14v10H1zM2 4l6 5 6-5v1L8 10 2 5z"/></svg>info@amberledge.example</li>
      <li><svg viewBox="0 0 16 16" aria-hidden="true"><circle cx="8" cy="8" r="7"/></svg>www.amberledge.example</li>
    </ul>
  </section>
</main>
</body>
</html>
```